Web redesign for Windows software

We're a small & dynamic development team.
Our website www.vantrelo.com hosts a popular, free application virtualization software for Windows.
This technology was complex to develop, yet simple to use.
We've been a Freeware soft so far, and now we want to introduce a commercial, paying version.

We want to make www.vantrelo.com look professional, and adapted to the new commercial requirements.

We like the homepage design of www.pluvex.com

We need a redesign of the homepage and a sample interior page.

Target Market(s)

Computer geeks

Industry/Entity Type

Software

Requirements
Must have
• - Must keep the same colors as current vantrelo.com (black, gray, gray, white)
- DOWNLOAD button must be the #1 goal
- Video should have a high-importance place (video not ready yet, but will be in this style: http://lnkr.example/QmzRt)
- Homepage should have buttons/links to: Personal, Business, Developers
- Full navigation on the bottom (Products, Blog, Forum, About, Contact etc)
- Login, Language buttons
- Image slider (i.e similar to the one on pluvex.com) with 3 images: a. intro: 'try apps without risking your system', b. try Windows apps without installing them, c. put your apps in the cloud, d. share apps to your IT users
Nice to have
• A slight refresh of the logo is welcome (i.e light / metal effect)

```html
<!DOCTYPE html>
<html lang="en">
<head>
<meta charset="utf-8">
<title>Vantrelo — Put your apps in the cloud</title>
<link href="https://fonts.googleapis.com/css2?family=Source+Sans+3:wght@300;400;600&display=swap" rel="stylesheet">
<style>
:root{
  --bar:#161616;
  --header:#272727;
  --header-dot:#333;
  --white:#fff;
  --subnav:#ececec;
  --ink:#333;
  --red:#b8210e;
  --blue:#3d86c0;
  --rule:#dcdcdc;
  --ui:"Source Sans 3", sans-serif;
  --body:Arial, Helvetica, sans-serif;
}
*{box-sizing:border-box;margin:0;padding:0}
html,body{width:1200px;height:1089px;overflow:hidden;background:var(--white)}
.stage{width:1150px;height:1044px;transform:scale(1.0435);transform-origin:0 0;position:relative;font-family:var(--ui);color:var(--ink)}
.abs{position:absolute}
.topbar{left:0;top:0;width:1150px;height:53px;background:var(--bar)}
.header{left:0;top:53px;width:1150px;height:435px;background-color:var(--header);
  background-image:radial-gradient(var(--header-dot) 1px,transparent 1.4px);background-size:6px 6px}
.page-fade{left:0;top:488px;width:1150px;height:60px;background:linear-gradient(#e9e9e9,#fff)}
.lang-label{left:681px;top:19px;font-size:13px;color:#aaa}
.lang-select{left:750px;top:14px;width:99px;height:26px;background:#fff;border-radius:3px;font-size:13px;color:#333;padding:4px 0 0 37px}
.lang-select .flag{position:absolute;left:9px;top:7px;width:19px;height:12px;background:#2a3f86}
.lang-select .caret{position:absolute;right:9px;top:6px;font-size:10px}
.user{left:872px;top:18px;font-size:14px;color:#ccc}
.user span{margin:0 8px;color:#777}
.logo{left:85px;top:62px;font-size:46px;font-weight:300;color:#f2f2f2;letter-spacing:4px}
.share{top:78px;height:19px;font-size:11px;color:#333;display:flex;gap:3px}
.share b{background:#eef1f6;border:1px solid #c6cad3;border-radius:2px;padding:1px 6px;font-weight:600}
.share i{font-style:normal;background:#fff;border:1px solid #bbb;border-radius:2px;padding:1px 4px}
.search{left:872px;top:73px;width:193px;height:30px;background:#fff;border:1px solid #ccc;border-radius:2px;font-size:12px;font-style:italic;color:#999;padding:7px 10px}
.panel{left:86px;top:128px;width:979px;height:362px;background:#fff;border:2px solid #eee;border-radius:3px;overflow:hidden}
.tabs{left:0;top:0;width:975px;height:57px;background:linear-gradient(#4a4a4a,#2e2e2e);display:flex}
.tab{height:57px;padding:21px 0 0;font-size:15px;color:#bbb;text-align:center;border-right:1px solid #1d1d1d}
.tab.active{background:#1c1c1c;color:#fff}
.download{left:786px;top:8px;width:180px;height:38px;border-radius:20px;background:#1a1a1a;padding:3px}
.download div{height:32px;border-radius:16px;background:linear-gradient(#f0602c,#c52a08);color:#fff;font-size:15px;font-weight:600;padding:6px 0 0 14px}
.download svg{position:absolute;right:14px;top:14px}
.subnav{left:0;top:57px;width:975px;height:42px;background:var(--subnav);font-size:13px;color:#333;padding:13px 0 0 35px;word-spacing:2px}
.subnav span{margin:0 17px;color:#555}
.slide{left:0;top:99px;width:975px;height:263px;background:linear-gradient(90deg,#fff 30%,#f0f0f0)}
.art{left:58px;top:32px;width:240px;height:195px;border-radius:14px;background:radial-gradient(circle at 60% 60%,#5cb4ec,#d8d8d8 70%,#f6f6f6)}
.slide h1{left:364px;top:30px;font-size:43px;font-weight:300;color:#222;white-space:nowrap}
.slide h1 em{font-style:normal;color:var(--blue)}
.slide p{left:364px;top:104px;width:380px;font-family:var(--body);font-size:12px;line-height:20px;color:#666;text-align:justify}
.badge{left:770px;top:112px;width:78px;height:36px;background:#2a2a2a;border-radius:3px}
.try{left:366px;top:178px;width:132px;height:38px;border-radius:3px;background:linear-gradient(#555,#333);color:#fff;font-size:15px;font-weight:600;padding:9px 0 0 16px}
.dots{left:878px;top:222px;display:flex;gap:8px}
.dots i{width:13px;height:13px;border-radius:50%;background:#bbb}
.dots i:first-child{background:#444}
.welcome{left:96px;top:512px;font-size:22px;font-weight:400;color:var(--red)}
.intro{left:94px;top:551px;width:589px;font-family:var(--body);font-size:12px;line-height:22px;color:#444;text-align:justify;letter-spacing:-0.1px}
.intro p{margin-bottom:8px}
.video{left:710px;top:519px;width:345px;height:197px;background:#000;padding:3px;box-shadow:0 10px 14px -8px rgba(0,0,0,.4)}
.screen{width:339px;height:173px;background:linear-gradient(#4a4a4a,#3c3c3c);position:relative}
.play{position:absolute;left:150px;top:68px}
.progress{height:5px;background:#555;position:relative}
.progress i{position:absolute;left:0;top:0;width:80px;height:5px;background:#d10000}
.controls{height:16px;font-size:6px;color:#ccc;padding:4px 8px;background:#1a1a1a;display:flex;justify-content:space-between}
.hr{height:1px;background:var(--rule);left:86px;width:979px}
.feature{top:786px;width:300px}
.feature h2{font-size:22px;font-weight:400;color:var(--red);display:flex;align-items:center;gap:10px;height:44px;white-space:nowrap}
.feature p{margin-top:13px;font-family:var(--body);font-size:12px;line-height:20px;color:#333;text-align:justify}
.vline{top:788px;width:1px;height:133px;background:var(--rule)}
.footnav{left:87px;top:978px;font-size:13px;color:#222}
.footnav span{margin:0 7px;color:#555}
.copy{left:87px;top:1008px;font-size:13px;color:#222}
.social{top:988px;width:28px;height:28px;border-radius:3px;background:#7a7a7a}
</style>
</head>
<body>
<div class="stage">
  <div class="abs topbar"></div>
  <div class="abs header"></div>
  <div class="abs page-fade"></div>

  <div class="abs lang-label">Language :</div>
  <div class="abs lang-select"><span class="flag"></span>English<span class="caret">&#9660;</span></div>
  <div class="abs user">Welcome, Username<span>|</span>Sign Out</div>

  <div class="abs logo">VANTRELO</div>
  <div class="abs share" style="left:685px"><b>Like</b><i>3k</i></div>
  <div class="abs share" style="left:763px"><b>Tweet</b><i>316</i></div>
  <div class="abs search">Search</div>

  <div class="abs panel">
    <div class="abs tabs">
      <div class="tab active" style="width:141px">PERSONAL</div>
      <div class="tab" style="width:130px">BUSINESS</div>
      <div class="tab" style="width:151px">DEVELOPERS</div>
    </div>
    <div class="abs download"><div>DOWNLOAD NOW</div>
      <svg width="14" height="14" viewBox="0 0 14 14"><circle cx="7" cy="7" r="7" fill="#3a1005"/><path d="M7 3v6M4.5 6.5 7 9.5l2.5-3" stroke="#fff" stroke-width="1.6" fill="none"/></svg>
    </div>
    <div class="abs subnav">Blog<span>|</span>Forum<span>|</span>About<span>|</span>Contact us<span>|</span>Help<span>|</span>FAQ</div>
    <div class="abs slide">
      <div class="abs art" role="img" aria-label="Illustration of a toolbox with tools on a blue cloud"></div>
      <h1 class="abs">Put your apps in the <em>cloud</em>...</h1>
      <p class="abs">Duis aute irure dolor in reprehenderit in voluptate velit esse cillum dolore eu fugiat nulla pariatur. Excepteur sint occaecat cupidatat non proident, sunt in culpa qui officia deserunt.</p>
      <div class="abs badge"></div>
      <div class="abs try">TRY NOW
        <svg class="abs" style="right:12px;top:10px" width="18" height="18" viewBox="0 0 18 18"><circle cx="9" cy="9" r="9" fill="#111"/><path d="M5 9h7M9 6l3 3-3 3" stroke="#fff" stroke-width="1.6" fill="none"/></svg>
      </div>
      <div class="abs dots"><i></i><i></i><i></i><i></i></div>
    </div>
  </div>

  <h2 class="abs welcome">Welcome to our site</h2>
  <div class="abs intro">
    <p>&nbsp;virtual app (or portable app) is a single .EXE file that holds an entire application, including files, DLLs and registry. Virtual apps can be copied &amp; moved around like regular files and launched from anywhere without installation: home, office, CloudLocker, USB disk-on-key, laptop, network shares. With Vantrelo's app virtualization, you can take your apps and data with you, anywhere.</p>
    <p>With Vantrelo's application virtualization, you can package an entire application - including all its files, DLLs, registry - into one single file and take it with you anywhere, along with the app's settings &amp; data. On your CloudLocker drive, on a USB stick, at work, at home, on your laptop - using application virtualization you will no longer have to reinstall your apps again and again everytime you move from one computer to another.</p>
  </div>

  <div class="abs video">
    <div class="screen" role="img" aria-label="Video still from the animated product explainer">
      <svg class="play" width="44" height="40" viewBox="0 0 44 40"><rect width="44" height="40" rx="10" fill="#111"/><path d="M17 12v16l13-8z" fill="#fff"/></svg>
    </div>
    <div class="progress"><i></i></div>
    <div class="controls"><span>&#10074;&#10074; &#9654; 0:02 / 0:10</span><span>720p</span></div>
  </div>

  <div class="abs hr" style="top:765px"></div>

  <div class="abs feature" style="left:86px">
    <h2><svg width="52" height="40" viewBox="0 0 52 40"><path d="M2 4h14l4 4h20v26H2z" fill="#3aa845"/><path d="M14 14v12M9 21l5 6 5-6" stroke="#fff" stroke-width="3" fill="none"/><circle cx="40" cy="28" r="10" fill="#e02020"/><path d="M36 24l8 8M44 24l-8 8" stroke="#fff" stroke-width="2.5"/></svg>Stop Installing apps</h2>
    <p>Sed ut perspiciatis unde omnis iste natus error sit voluptatem accusantium doloremque laudantium, totam rem aperiam, eaque ipsa quae ab illo inventore veritatis et quasi architecto beatae vitae dicta.</p>
  </div>
  <div class="abs vline" style="left:406px"></div>
  <div class="abs feature" style="left:427px">
    <h2><svg width="42" height="40" viewBox="0 0 42 40"><path d="M30 3a9 9 0 0 0-8 12L4 32l4 4 18-17a9 9 0 0 0 12-8l-6 3-4-4 3-6z" fill="#2a86d8"/></svg>Easy Settings</h2>
    <p>Sed ut perspiciatis unde omnis iste natus error sit voluptatem accusantium doloremque laudantium, totam rem aperiam, eaque ipsa quae ab illo inventore veritatis et quasi architecto beatae vitae dicta.</p>
  </div>
  <div class="abs vline" style="left:748px"></div>
  <div class="abs feature" style="left:768px">
    <h2><svg width="42" height="40" viewBox="0 0 42 40"><path d="M8 18a13 13 0 0 1 23-8l3-3v11H23l4-4a8 8 0 0 0-14 4z" fill="#f07a20"/><path d="M34 22a13 13 0 0 1-23 8l-3 3V22h11l-4 4a8 8 0 0 0 14-4z" fill="#e85a10"/></svg>Share apps to your IT users</h2>
    <p>Sed ut perspiciatis unde omnis iste natus error sit voluptatem accusantium doloremque laudantium, totam rem aperiam, eaque ipsa quae ab illo inventore veritatis et quasi architecto beatae vitae dicta.</p>
  </div>

  <div class="abs hr" style="top:955px"></div>
  <div class="abs footnav">Home<span>|</span>About us<span>|</span>personal<span>|</span>Business<span>|</span>Developers<span>|</span>Contact us</div>
  <div class="abs copy">Copyright © 2012 www.vantrelo.com&nbsp;&nbsp; All rights reserved.</div>
  <div class="abs social" style="left:996px"></div>
  <div class="abs social" style="left:1037px"></div>
</div>
</body>
</html>
```